Web Design Project

I need a three page website. I have designed the index.html and the specialevent.html page.

I need someone to finetune the pages for me.

Where I have difficulty is with the following:
I want to add an event table driven by php database.
The administrator of the event will login and create the wording that fits under each colmn. The administrator the submit the form to php database. The database then display in a html.

The Table contains 5 coloums and the rows can vary and can go up to as many as 100.

The table set out events on a program
In the last column of every row I need a submit button to "View and Book" I need to link those buttons with external links/pages.

I use Dreamweaver CS5 and I need to have it in this format in order for me to edit it in the future.

The Table needs to be updated once a year for this program. So ideally if someone has a password to update the certain regions this is what I have in mind.

I have also designed a mockup of the restaurant page. At the top I need.
1) 4 Colapsable panels
a) Restaurants - opening the names of the restaurants
b) Coffee shops and light lunches .... with the names
c) Family
d) Home eateries

From the colapsable panel of each of these I need a anchored link to the description/photos of each...with a BOOK now button I can submit bookings to.

I added a colapsable panel in each restaurants description to keep everything contained.

Please help

• Background must be fixed so that main.div scroll over it

The colours are chosen so please stick to it.

The green for the submit button I short is. #C8D707

I need to edit the pages in Dreamweaver CS5. /Flexilayout2pro

Please ask if you need to know anything. I exactly know what I want.

Kind regards
Pieter Vansloten

The colours are fine.

The wording " karoovistadirect BOOKING agent" should appear right at the top in the white horizon part of the background image.

The specialevent page I described already. I am interested in the editable solution. for this.

I will make up a mockup of the third page and send it later.

Regards

```html
<!DOCTYPE html>
<html lang="en">
<head>
<meta charset="utf-8">
<title>karoovistadirect – Home</title>
<link rel="stylesheet" href="https://fonts.googleapis.com/css2?family=Anton&family=Ubuntu:wght@400;500&family=Roboto:wght@400;700&display=swap">
<style>
:root{
  --lime:#c8d707;
  --lime-text:#b8c400;
  --bar:#4b4e52;
  --bar-dark:#3d4044;
  --ink:#1f1f1f;
  --soft-ink:#333;
  --panel:#eef3bb;
  --footer:#eeeeee;
  --line:#c9c9c9;
  --white:#fff;
}
*{box-sizing:border-box;margin:0;padding:0}
html,body{width:1200px;height:1172px;overflow:hidden;background:var(--white)}
body{position:relative;font-family:"Ubuntu",sans-serif;color:var(--ink)}
.abs{position:absolute}

.top-strip{left:0;top:0;width:1200px;height:24px;background:linear-gradient(#fafafa,#e9e9e9)}
.follow{right:140px;top:3px;font-size:13px;color:#333;display:flex;align-items:center;gap:5px}
.follow span{margin-right:8px}
.social{width:18px;height:18px;display:inline-block}
.s1{background:#3b5a9a}.s2{background:#1b86c4}.s3{background:#d4241c}

.hero{left:0;top:24px;width:1200px;height:594px;background:linear-gradient(180deg,#5a5a58 0%,#8d8c86 30%,#a9a8a2 55%,#77776f 80%,#8a8a84 100%)}
.navbar{left:0;top:24px;width:1200px;height:71px;background:linear-gradient(var(--bar),var(--bar-dark));opacity:.95}
.brand{left:147px;top:30px;font-family:"Ubuntu",sans-serif;font-weight:500;font-size:30px;color:var(--lime);display:flex;align-items:center;gap:8px}
.brand i{width:16px;height:16px;border-radius:50%;background:var(--lime);display:inline-block}
.nav{left:602px;top:40px;display:flex;align-items:center;font-size:16px;color:var(--white)}
.nav a{color:var(--white);text-decoration:none;padding:9px 27px 7px}
.nav a.active{background:var(--lime);color:var(--ink);padding:9px 28px 8px}
.nav a:nth-child(2){padding-left:18px}

.hero-title{left:0;width:1200px;top:192px;text-align:center;font-family:"Anton",sans-serif;font-size:74px;line-height:1;color:var(--white);letter-spacing:-1px;text-shadow:0 2px 6px rgba(0,0,0,.35)}
.hero-sub{left:0;width:1200px;top:282px;text-align:center;font-family:"Anton",sans-serif;font-size:34px;color:var(--white);text-shadow:0 0 3px #222,0 0 2px #222}
.arrow{top:249px;width:34px;height:34px}
.arrow.prev{left:146px}.arrow.next{left:1020px}

.tagline{left:143px;top:462px;width:915px;height:48px;background:linear-gradient(rgba(80,82,86,.55),rgba(60,62,66,.9));color:var(--white);text-align:center;font-size:32px;line-height:50px}

.card{top:518px;width:295px;height:245px;background:var(--white);border:1px solid var(--line)}
.card .pic{position:absolute;left:13px;top:13px;width:269px;height:118px}
.card h2{position:absolute;left:11px;top:139px;font-weight:400;font-size:23px}
.card p{position:absolute;left:11px;top:174px;right:4px;font-size:12px;line-height:16.6px;letter-spacing:1px;color:var(--soft-ink)}
.c1{left:143px}.c2{left:454px}.c3{left:763px}
.c2 h2{top:143px}

.events{left:143px;top:795px;width:915px;height:168px;background:var(--panel);border:1px solid #dfe5a8}
.events h2{position:absolute;left:0;width:100%;top:5px;text-align:center;font-weight:400;font-size:22px}
.events .inner{position:absolute;left:10px;top:42px;width:893px;height:112px;background:var(--white)}
.event{position:absolute;top:0;height:112px}
.event h3{position:absolute;left:0;top:6px;font-weight:400;font-size:17px;white-space:nowrap}
.event .date{position:absolute;right:0;top:7px;font-size:13px;color:var(--lime-text);white-space:nowrap}
.event hr{position:absolute;left:0;right:0;top:31px;border:0;border-top:1px solid #ccc}
.event p{position:absolute;left:0;right:0;top:38px;font-size:12px;line-height:16.6px;letter-spacing:.6px;color:var(--soft-ink)}
.event .btn{position:absolute;right:0;bottom:5px}
.e1{left:12px;width:424px}.e2{left:462px;width:422px}
.divider{position:absolute;left:449px;top:16px;height:90px;border-left:1px dotted #aab04a}
.btn{background:var(--lime);color:var(--ink);font-size:14px;padding:4px 15px;display:inline-block}

.footer{left:0;top:987px;width:1200px;height:137px;background:var(--footer)}
.col{top:1004px}
.col h4{font-weight:400;font-size:17px;margin-bottom:16px}
.col li{list-style:none;font-family:"Roboto",sans-serif;font-size:12.5px;line-height:18.5px;letter-spacing:.3px}
.f1{left:144px}.f2{left:376px}.f3{left:566px}
.field{width:217px;height:28px;border:1px solid #ccc;background:var(--white);font-family:"Roboto",sans-serif;font-size:11px;color:#999;padding:6px 10px}
.f3 .btn{margin-top:9px;padding:3px 15px}
.contact{left:854px;top:998px;font-family:"Roboto",sans-serif}
.contact .phone{font-family:"Ubuntu",sans-serif;font-size:27px;margin-bottom:4px}
.contact p{font-size:12.5px;line-height:20px;margin-left:2px}
.copy-band{left:0;top:1124px;width:1200px;height:48px;background:linear-gradient(#fbfbfb,#f0f0f0)}
.copy{left:148px;top:1144px;font-family:"Roboto",sans-serif;font-size:10px;color:#555}
</style>
</head>
<body>
<div class="abs top-strip"></div>
<div class="abs follow"><span>Follow us</span><i class="social s1"></i><i class="social s2"></i><i class="social s3"></i></div>

<div class="abs hero" role="img" aria-label="Black and white photograph of a small Karoo town with a white church, trees and a road winding into the mountains"></div>

<header class="abs navbar"></header>
<div class="abs brand">karoovistadirect<i></i></div>
<nav class="abs nav"><a class="active">Home</a><a>Accommodation</a><a>Excursions</a><a>Contact</a></nav>

<h1 class="abs hero-title">welcome to our website</h1>
<div class="abs hero-sub">karoovistadirect</div>
<svg class="abs arrow prev" viewBox="0 0 34 34"><circle cx="17" cy="17" r="15.5" fill="#2c2c2c" stroke="#fff" stroke-width="2.5"/><path d="M18 11l-6 6 6 6M24 11l-6 6 6 6" fill="none" stroke="#fff" stroke-width="3"/></svg>
<svg class="abs arrow next" viewBox="0 0 34 34"><circle cx="17" cy="17" r="15.5" fill="#2c2c2c" stroke="#fff" stroke-width="2.5"/><path d="M10 11l6 6-6 6M16 11l6 6-6 6" fill="none" stroke="#fff" stroke-width="3"/></svg>

<div class="abs tagline">Your booking agent for</div>

<section class="abs card c1">
  <div class="pic" role="img" aria-label="Photograph of a colourful coastal village on cliffs above blue sea" style="background:linear-gradient(160deg,#5b8fc4,#2a6ca8 45%,#a87a5e 75%,#6c6a50)"></div>
  <h2>Book Stay</h2>
  <p>Find &nbsp;the perfect accommodation to suit your specific needs. Click on &nbsp;bookStay to view and book our properties online NOW!</p>
</section>
<section class="abs card c2">
  <div class="pic" role="img" aria-label="Photograph of a DJ performing under bright stage lights" style="background:radial-gradient(circle at 35% 35%,#f3c54a,#b3641a 40%,#2a1506 85%)"></div>
  <h2>Book Play</h2>
  <p>&nbsp;Secure your Playlist! Vistadorp has wonderful excursions, activities, shows and festivals on offer. Click on bookPlay and book it all ONLINE!</p>
</section>
<section class="abs card c3">
  <div class="pic" role="img" aria-label="Photograph of a green salad with apple slices and croutons" style="background:radial-gradient(circle at 50% 45%,#c7d86a,#6d8f2c 50%,#1f2a14 95%)"></div>
  <h2>Book Eat</h2>
  <p>Wow! Book your eating experience with us. As always Vistadorp has the best on offer to enhance your cullinary experience. Click bookEat!</p>
</section>

<section class="abs events">
  <h2>Special events and Festivals</h2>
  <div class="inner">
    <article class="event e1">
      <h3>Olive Festival - April 2014</h3><span class="date">1 Aprail</span><hr>
      <p>Vistadorp promises to once again offer a delightful and exhilirating Olive Festival in April 2014. View the Olive Festival Programme and BOOK all your activies with us ONLINE!</p>
      <span class="btn">Read More</span>
    </article>
    <div class="divider"></div>
    <article class="event e2">
      <h3>Winter School - August 2014</h3><span class="date">1 Augest</span><hr>
      <p>As soon as the riveting Winter School Programme is finalised for 2014, we will inform you. Please subscribe to our newsletter to receive updated information on all our events. ....</p>
      <span class="btn">Read More</span>
    </article>
  </div>
</section>

<footer class="abs footer"></footer>
<div class="abs col f1"><h4>Services</h4><ul><li>Bussiness directory</li><li>Relevant links and websites</li><li>Emergency Numbers</li></ul></div>
<div class="abs col f2"><h4>Useful Links</h4><ul><li>About us</li><li>FAQs</li><li>Disclaimer</li></ul></div>
<div class="abs col f3"><h4>Newsletter Sign-Up</h4><div class="field">Email</div><span class="btn">Send</span></div>
<div class="abs contact"><div class="phone">0800 123 456</div><p>Kerk Street, Vistadorp</p><p><b>Email:</b> admin@karoovista.example</p></div>
<div class="abs copy-band"></div>
<div class="abs copy">© 2013 karoovista. All Rights Reserved.</div>
</body>
</html>
```